WordPress Design for both website and landing page for an expert

I need a clean and stylish design for my new website. I work as an expert (see attached file WHY HOW WHAT), my product is expert opinion (reports) for company evaluations You can use all of the attached pictures colored or black / white. The person is me, you can add other pictures, if you want. The design should be clean and stylish, so you could use white, black, gray, silver and / or one additional color. I have added an idea about my website, see attached file CONCEPT WEBSITE If you have any more information, please do not hesitate to contact us 'Hesitate to ask me ...

```html
<!DOCTYPE html>
<html lang="de">
<head>
<meta charset="utf-8">
<title>Lars Vennemann – Sachverständiger für Firmenbewertungen</title>
<link rel="stylesheet" href="https://fonts.googleapis.com/css2?family=Montserrat:wght@500;600;700&family=Roboto:wght@400;500;700&display=swap">
<style>
  :root{
    --black:#000;
    --white:#fff;
    --ink:#111;
    --grey-dark:#2a2a2a;
    --grey-mid:#555;
    --silver:#c9c9c9;
    --text-muted:#333;
  }
  *{box-sizing:border-box;margin:0;padding:0}
  html,body{width:1200px;height:3186px;overflow:hidden}
  body{position:relative;font-family:'Roboto',Arial,sans-serif;color:var(--white);background:var(--black)}
  .section{position:absolute;left:0;width:1200px}
  .abs{position:absolute}

  /* header */
  .site-header{top:0;height:140px;background:var(--black)}
  .brand{left:92px;top:44px;display:flex;align-items:center;gap:14px}
  .brand__square{width:26px;height:26px;background:var(--silver)}
  .brand__name{font-family:'Montserrat',Arial,sans-serif;font-weight:500;font-size:29px;letter-spacing:4px;color:var(--silver);text-transform:uppercase}
  .main-nav{right:97px;top:65px;display:flex;gap:32px}
  .main-nav a{color:var(--white);text-decoration:none;font-weight:700;font-size:16px}

  /* hero */
  .hero{top:140px;height:582px;background:linear-gradient(90deg,#3b3b3b 0%,#6c6c6c 35%,#9a9a9a 60%,#5c5c5c 85%,#444 100%)}
  .hero__title{left:90px;top:200px;font-family:'Montserrat',Arial,sans-serif;font-weight:700;font-size:56px;line-height:64px}
  .hero__sub{left:90px;top:356px;font-size:17px}

  /* benefits */
  .benefits{top:722px;height:569px;background:var(--black)}
  .benefits__title{top:74px;width:100%;text-align:center;font-family:'Montserrat',Arial,sans-serif;font-weight:700;font-size:36px}
  .hex{top:204px;width:330px;height:285px}
  .hex svg.hex__frame{position:absolute;inset:0}
  .hex__icon{position:absolute;left:125px;top:10px;width:80px;height:80px}
  .hex__title{position:absolute;top:124px;width:100%;text-align:center;font-weight:700;font-size:18px}
  .hex__text{position:absolute;top:152px;left:60px;width:210px;text-align:center;font-size:14.5px;line-height:27px}

  /* faq */
  .faq{top:1291px;height:638px;background:linear-gradient(160deg,#3c3c3c 0%,#555 40%,#6d6d6d 70%,#4a4a4a 100%)}
  .faq__title{top:68px;width:100%;text-align:center;font-family:'Montserrat',Arial,sans-serif;font-weight:700;font-size:36px}
  .faq-item{left:170px;width:862px;background:var(--white);border-radius:8px;color:var(--ink)}
  .faq-item__q{position:absolute;left:20px;right:70px;font-weight:700;font-size:19px;line-height:24px}
  .faq-item__a{position:absolute;left:34px;top:58px;width:520px;font-size:15px;line-height:27px;color:var(--text-muted)}
  .faq-item__chev{position:absolute;right:30px;width:24px;height:24px}

  /* about */
  .about{top:1929px;height:486px;background:var(--white);color:var(--ink)}
  .about__photo{left:89px;top:84px;width:497px;height:340px;background:linear-gradient(100deg,#d9d9d9 0%,#bdbdbd 45%,#e6e6e6 100%)}
  .about__frame{left:107px;top:100px;width:461px;height:308px;border:3px solid var(--white)}
  .about__title{left:616px;top:110px;font-family:'Montserrat',Arial,sans-serif;font-weight:700;font-size:36px}
  .about__text{left:612px;top:196px;width:500px;font-size:18px;line-height:27.5px}

  /* promise */
  .promise{top:2415px;height:370px;background:linear-gradient(180deg,#1c1c1c 0%,#2e2e2e 60%,#222 100%);text-align:center}
  .promise__h{width:100%;font-family:'Montserrat',Arial,sans-serif;font-weight:700;font-size:29px}
  .promise__p{width:100%;font-size:17px}
  .btn{left:457px;width:252px;height:49px;background:var(--white);color:var(--ink);border-radius:8px;font-size:17px;line-height:49px;text-align:center}

  /* footer */
  .site-footer{top:2785px;height:401px;background:var(--black)}
  .site-footer .brand{left:92px;top:225px}
  .footer__h{font-family:'Montserrat',Arial,sans-serif;font-weight:700;font-size:29px;top:72px}
  .footer__links{left:487px;top:124px;list-style:none}
  .footer__links li{font-size:16px;line-height:32.5px}
  .newsletter__text{left:763px;top:124px;width:220px;font-size:16px;line-height:28px}
  .newsletter__input{left:763px;top:191px;width:204px;height:36px;background:var(--white);color:var(--ink);font-size:13px;padding:11px 6px}
  .newsletter__btn{left:763px;top:248px;width:83px;height:31px;background:var(--white);color:var(--ink);border-radius:6px;font-size:16px;line-height:31px;text-align:center}
  .copyright{top:356px;width:100%;text-align:center;font-size:16px}
</style>
</head>
<body>

<header class="section site-header">
  <div class="abs brand"><span class="brand__square"></span><span class="brand__name">Lars Vennemann</span></div>
  <nav class="abs main-nav">
    <a href="#">Home</a><a href="#">What I Do</a><a href="#">Why I Do It &amp; How I Do It</a><a href="#">About Me</a><a href="#">Contact</a>
  </nav>
</header>

<section class="section hero" role="img" aria-label="Portrait photo of the expert in a dark suit standing in a bright modern corridor">
  <h1 class="abs hero__title">Sachverständiger für<br>Firmenbewertungen</h1>
  <p class="abs hero__sub">Sie benötigen ein Gutachten zur Ermittlung des Wertes Ihres Unternehmens</p>
</section>

<section class="section benefits">
  <h2 class="abs benefits__title">Why you should work with me</h2>

  <div class="abs hex" style="left:58px">
    <svg class="hex__frame" viewBox="0 0 330 285"><polygon points="80,2 250,2 328,142 250,283 80,283 2,142" fill="none" stroke="#fff" stroke-width="3"/></svg>
    <svg class="hex__icon" viewBox="0 0 80 80" fill="none" stroke="#fff" stroke-width="3"><circle cx="48" cy="44" r="22"/><circle cx="48" cy="44" r="14"/><circle cx="48" cy="44" r="6"/><line x1="10" y1="44" x2="44" y2="44"/><line x1="14" y1="34" x2="24" y2="34"/><line x1="14" y1="54" x2="24" y2="54"/></svg>
    <div class="hex__title">Schnell</div>
    <div class="hex__text">Sie bekommen Ihr Gutachten zeitnah</div>
  </div>

  <div class="abs hex" style="left:436px">
    <svg class="hex__frame" viewBox="0 0 330 285"><polygon points="80,2 250,2 328,142 250,283 80,283 2,142" fill="none" stroke="#fff" stroke-width="3"/></svg>
    <svg class="hex__icon" viewBox="0 0 80 80" fill="none" stroke="#fff" stroke-width="3"><rect x="6" y="8" width="68" height="48"/><line x1="18" y1="22" x2="62" y2="22"/><line x1="18" y1="32" x2="44" y2="32"/><circle cx="56" cy="52" r="10"/><polyline points="50,60 48,76 56,70 64,76 62,60"/></svg>
    <div class="hex__title">Zertifiziert</div>
    <div class="hex__text">Sie erhalten ein qualifiziertes und belastbares Gutachten von einem zertifizierten Sachverständigen</div>
  </div>

  <div class="abs hex" style="left:781px">
    <svg class="hex__frame" viewBox="0 0 330 285"><polygon points="80,2 250,2 328,142 250,283 80,283 2,142" fill="none" stroke="#fff" stroke-width="3"/></svg>
    <svg class="hex__icon" viewBox="0 0 80 80" fill="none" stroke="#fff" stroke-width="3"><circle cx="40" cy="30" r="16"/><line x1="33" y1="50" x2="47" y2="50"/><line x1="34" y1="56" x2="46" y2="56"/><line x1="40" y1="4" x2="40" y2="9"/><line x1="14" y1="30" x2="19" y2="30"/><line x1="61" y1="30" x2="66" y2="30"/><line x1="20" y1="12" x2="24" y2="16"/><line x1="60" y1="12" x2="56" y2="16"/><line x1="12" y1="70" x2="68" y2="70"/></svg>
    <div class="hex__title">Verständlich</div>
    <div class="hex__text">Ihr Gutachten wird für Sie logisch und nachvollziehbar sein und kein "Fachchinesisch" enthalten</div>
  </div>
</section>

<section class="section faq" aria-label="FAQ">
  <div class="abs" role="img" aria-label="Dark background photo of financial documents and a calculator" style="inset:0"></div>
  <h2 class="abs faq__title">FAQ</h2>

  <div class="abs faq-item" style="top:153px;height:138px">
    <div class="faq-item__q" style="left:34px;top:20px">What are the buying motives of the customers?</div>
    <p class="faq-item__a">It is a long established fact that a reader will be distracted by the readable content of a page when looking at its layout.</p>
    <svg class="faq-item__chev" style="top:18px" viewBox="0 0 24 24" fill="none" stroke="#111" stroke-width="3.5"><polyline points="4,16 12,8 20,16"/></svg>
  </div>

  <div class="abs faq-item" style="top:313px;height:59px">
    <div class="faq-item__q" style="top:17px">Was sind die Kaufmotive der Kunden?</div>
    <svg class="faq-item__chev" style="top:18px" viewBox="0 0 24 24" fill="none" stroke="#111" stroke-width="3.5"><polyline points="4,8 12,16 20,8"/></svg>
  </div>

  <div class="abs faq-item" style="top:398px;height:59px">
    <div class="faq-item__q" style="top:6px">Sie wollen Ihr Unternehmen auf Ihre Erben übertragen und benötigen eine Bewertung für das Finanzamt?</div>
    <svg class="faq-item__chev" style="top:18px" viewBox="0 0 24 24" fill="none" stroke="#111" stroke-width="3.5"><polyline points="4,8 12,16 20,8"/></svg>
  </div>

  <div class="abs faq-item" style="top:478px;height:89px">
    <div class="faq-item__q" style="top:18px">Sie müssen im Rahmen einer Trennung/Scheidung jemanden auszubezahlen und benötigen eine Bemessungsgrundlage?</div>
    <svg class="faq-item__chev" style="top:20px" viewBox="0 0 24 24" fill="none" stroke="#111" stroke-width="3.5"><polyline points="4,8 12,16 20,8"/></svg>
  </div>
</section>

<section class="section about">
  <div class="abs about__photo" role="img" aria-label="Photo of the expert in a white shirt seated, leaning on a table"></div>
  <div class="abs about__frame"></div>
  <h2 class="abs about__title">About Me</h2>
  <p class="abs about__text">Lassen Sie Ihr Unternehmen von einem qualifizierten Sachverständigen bewerten und gehen somit vielen (unnötigen) Streitereien aus dem Weg.<br>Merke: Die Kosten für ein Gutachten sind immer überproportional günstiger als die Kosten für Rechtsstreitigkeiten. Und das losgelöst von der psychischen Belastung einer solchen Auseinandersetzung ...</p>
</section>

<section class="section promise">
  <h2 class="abs promise__h" style="top:30px">My quality promise</h2>
  <p class="abs promise__p" style="top:84px">Should the advised date for the preparation of the report be exceeded, you will receive the report free of chare</p>
  <div class="abs btn" style="top:127px">I waive my fee</div>
  <h2 class="abs promise__h" style="top:202px">Mein Qualitätsversprechen</h2>
  <p class="abs promise__p" style="top:257px">Sollte der avisierte Termin für die Erstellung des Gutachtens überschritten werden, erhalten Sie das Gutachten absolut kostenfrei!</p>
  <div class="abs btn" style="top:295px">Ich verzichte auf mein Honorar</div>
</section>

<footer class="section site-footer">
  <div class="abs brand"><span class="brand__square"></span><span class="brand__name">Lars Vennemann</span></div>
  <h3 class="abs footer__h" style="left:486px">Quick Link</h3>
  <ul class="abs footer__links">
    <li>Home</li><li>What I Do</li><li>Why I Do It &amp; How I Do It</li><li>About Me</li><li>Contact</li>
  </ul>
  <h3 class="abs footer__h" style="left:763px">Newsletter</h3>
  <p class="abs newsletter__text">Register your email for news for Lars Vennemann</p>
  <div class="abs newsletter__input">Enter the email</div>
  <div class="abs newsletter__btn">Submit</div>
  <p class="abs copyright">Copyright © 2018 Lars Vennemann All Rights Reserved.</p>
</footer>

</body>
</html>
```